Communication and Marketing agency needs a new presentation card

We are a group of communication and marketing agencies specialized in companies that are in the logistics and industrial sector. The head agency is TELVANO Grupo and the group consists of 4 agencies: TELVANO Media, TELVANO Digital, TELVANO Research and DifundeEnPantalla. We hace 4 offices in Spain (Madrid, Barcelona, Valencia and Murcia). We are looking for a clean and attractive design that transmits our experience, brand presence in the market and knowledge to those who receive the card.It has to maintain the colors of the logo that is attached.
Target Market(s)
logistics and industrial sector
Marketing department
Contact Information for Business Card
Clean and attractive design

```html
<!DOCTYPE html>
<html lang="es">
<head>
<meta charset="utf-8">
<title>TELVANO Grupo – Tarjeta de presentación</title>
<link rel="stylesheet" href="https://fonts.googleapis.com/css2?family=Open+Sans:wght@400;600;700&display=swap">
<style>
  :root {
    --stage: #3a3431;
    --card-black: #0e0e0e;
    --brand-red: #b81c27;
    --silver: #c9c9c9;
    --text-light: #e6e6e6;
    --divider: #2c2c2c;
  }
  * { box-sizing: border-box; margin: 0; padding: 0; }
  html, body {
    width: 1200px; height: 844px; overflow: hidden;
    background: var(--stage);
    font-family: "Open Sans", Arial, sans-serif;
  }
  .stage {
    width: 1200px; height: 844px;
    display: flex; align-items: center; justify-content: center; gap: 60px;
  }
  .card {
    position: relative;
    width: 520px; height: 300px;
    background: var(--card-black);
    overflow: hidden;
    box-shadow: 0 10px 30px rgba(0,0,0,.45);
  }
  .card__band {
    position: absolute; left: 0; right: 0; bottom: 0;
    height: 84px;
    background: var(--brand-red);
  }
  .brand-name {
    font-weight: 600; letter-spacing: 1px; white-space: nowrap;
  }

  /* Back: contact side */
  .card--back .brand-name {
    position: absolute; left: 30px; top: 150px;
    width: 210px;
    font-size: 24px; line-height: 30px; color: var(--brand-red);
  }
  .card--back .divider {
    position: absolute; left: 258px; top: 40px;
    width: 1px; height: 148px; background: var(--divider);
  }
  .contact {
    position: absolute; left: 274px; top: 36px; right: 16px;
    color: var(--text-light); font-size: 13px; line-height: 19px;
  }
  .contact__name {
    color: var(--brand-red); font-weight: 700; font-size: 15px; letter-spacing: .5px;
  }
  .contact__role { margin-bottom: 4px; }
  .contact__line { display: flex; align-items: center; gap: 8px; white-space: nowrap; }
  .contact__line svg { width: 11px; height: 11px; fill: var(--brand-red); flex: none; }
  .contact__address { margin-top: 8px; padding-left: 19px; }
  .offices {
    display: flex; align-items: center; justify-content: center; height: 100%;
    color: var(--text-light); font-size: 14px; letter-spacing: 1px;
  }

  /* Front: brand side */
  .card--front .brand-name {
    position: absolute; left: 0; right: 0; top: 72px; text-align: center;
    font-size: 40px; color: var(--silver);
  }
  .agencies {
    display: flex; align-items: center; justify-content: space-around;
    height: 100%; padding: 0 14px;
    list-style: none;
  }
  .agencies li {
    color: #fff; font-weight: 600; font-size: 13px; letter-spacing: .3px; white-space: nowrap;
  }
</style>
</head>
<body>
<main class="stage">
  <section class="card card--back">
    <div class="brand-name">TELVANO Grupo</div>
    <div class="divider"></div>
    <div class="contact">
      <div class="contact__name">LUCAS FERRER</div>
      <div class="contact__role">Managing Director</div>
      <div class="contact__line">
        <svg viewBox="0 0 16 16"><path d="M3 1l3 3-2 2c1 2 3 4 5 5l2-2 3 3-2 3C6 14 2 10 1 4z"/></svg>
        044-987 650 312
      </div>
      <div class="contact__line">
        <svg viewBox="0 0 16 16"><path d="M4 0h8v16H4zM5.5 2v10h5V2z"/></svg>
        044-987 650 312
      </div>
      <div class="contact__line">
        <svg viewBox="0 0 16 16"><path d="M0 3h16v10H0zM1.5 4.5L8 9l6.5-4.5z"/></svg>
        info@telvanogrupo.es
      </div>
      <div class="contact__line">
        <svg viewBox="0 0 16 16"><circle cx="8" cy="8" r="7"/></svg>
        www.telvanogrupo.es
      </div>
      <div class="contact__address">12345, Address Goes Here<br>Country Name, 123456.</div>
    </div>
    <div class="card__band">
      <div class="offices">MADRID, BARCELONA, VALENCIA, MURCIA</div>
    </div>
  </section>

  <section class="card card--front">
    <div class="brand-name">TELVANO Grupo</div>
    <div class="card__band">
      <ul class="agencies">
        <li>TELVANO Research</li>
        <li>TELVANO Digital</li>
        <li>TELVANO Media</li>
        <li>DifundeEnPantalla</li>
      </ul>
    </div>
  </section>
</main>
</body>
</html>
```